I just need to get that same logo on the business card but with different word. “The Hinges Roadside and Rental”

Name: Marek T
Number: 4759028416
Email: thehingesroadside@brivomail.test

On the back, can we di just the logo and the hinges roadside and rental around it.

If possible a black card with the gold storefront type font that you used before, would be amazing. I attached the original logo just in case.

Target Market(s)

Roadside assistance

Industry/Entity Type

Repair/ roadside

Contact Information for Business Card

Name, email, phone number

Requirements
Must have
• Everything in description
Nice to have
• Nice big logo

```html
<!DOCTYPE html>
<html lang="en">
<head>
<meta charset="utf-8">
<title>The Hinges Roadside and Rental — Business Card</title>
<link href="https://fonts.googleapis.com/css2?family=Montserrat:wght@400;700;800&display=swap" rel="stylesheet">
<style>
  :root {
    --page-bg: #121213;
    --card-bg: #1d1d1f;
    --card-edge: #262628;
    --gold: #b48c4e;
    --gold-soft: #a07d45;
  }
  * { margin: 0; padding: 0; box-sizing: border-box; }
  html, body {
    width: 1200px;
    height: 857px;
    overflow: hidden;
    background: var(--page-bg);
    font-family: "Montserrat", sans-serif;
  }
  .stage {
    width: 1200px;
    height: 857px;
    display: flex;
    flex-direction: column;
    align-items: center;
    justify-content: center;
    gap: 44px;
  }
  .card {
    width: 560px;
    height: 320px;
    background: var(--card-bg);
    border: 1px solid var(--card-edge);
    border-radius: 4px;
    display: flex;
    flex-direction: column;
    align-items: center;
    justify-content: center;
    color: var(--gold);
  }

  /* Front: brand only */
  .brand {
    display: flex;
    align-items: center;
    gap: 16px;
  }
  .brand-square {
    width: 22px;
    height: 22px;
    background: var(--gold);
  }
  .brand-name {
    font-weight: 800;
    letter-spacing: 0.04em;
    text-transform: uppercase;
  }
  .card--front .brand-name { font-size: 44px; }

  /* Back: contact details */
  .card--info .brand-square { width: 14px; height: 14px; }
  .card--info .brand { gap: 10px; }
  .card--info .brand-name { font-size: 36px; }
  .tagline {
    font-weight: 400;
    font-size: 13px;
    letter-spacing: 0.16em;
    text-transform: uppercase;
    color: var(--gold-soft);
    margin-top: 4px;
  }
  .person {
    font-weight: 800;
    font-size: 30px;
    letter-spacing: 0.05em;
    text-transform: uppercase;
    margin-top: 26px;
  }
  .contact-icons {
    display: flex;
    gap: 8px;
    margin-top: 10px;
  }
  .contact-icons svg { width: 13px; height: 13px; fill: var(--gold); }
  .contact-line {
    font-weight: 400;
    font-size: 15px;
    letter-spacing: 0.06em;
    margin-top: 8px;
  }
  .contact-line + .contact-line { margin-top: 4px; }
</style>
</head>
<body>
  <main class="stage">
    <section class="card card--front" aria-label="Card front">
      <div class="brand">
        <span class="brand-square"></span>
        <span class="brand-name">The Hinges</span>
      </div>
    </section>

    <section class="card card--info" aria-label="Card back">
      <div class="brand">
        <span class="brand-square"></span>
        <span class="brand-name">The Hinges</span>
      </div>
      <p class="tagline">Roadside and Rental</p>
      <p class="person">Marek T</p>
      <div class="contact-icons">
        <svg viewBox="0 0 24 24" aria-hidden="true"><path d="M6.6 10.8a15.1 15.1 0 0 0 6.6 6.6l2.2-2.2a1 1 0 0 1 1-.25 11.4 11.4 0 0 0 3.6.57 1 1 0 0 1 1 1V20a1 1 0 0 1-1 1A17 17 0 0 1 3 4a1 1 0 0 1 1-1h3.5a1 1 0 0 1 1 1c0 1.25.2 2.45.57 3.57a1 1 0 0 1-.25 1z"/></svg>
        <svg viewBox="0 0 24 24" aria-hidden="true"><path d="M2 5h20v14H2z M2 5l10 8 10-8" /></svg>
      </div>
      <p class="contact-line">4759028416</p>
      <p class="contact-line">thehingesroadside@brivomail.test</p>
    </section>
  </main>
</body>
</html>
```